Wordpress Design for a Private Label BBQ Brand

For our new brand, we'd need a new Wordpress website. We'd prefer to run the website on Wordpress

We'd like to include the following
- space for description of the brand
- space for product portfolio (not a shop!)
- space for socials
- space for support
- space for contact

```html
<!DOCTYPE html>
<html lang="en">
<head>
<meta charset="utf-8">
<title>Fiammeo — Grills &amp; Barbecue</title>
<link href="https://fonts.googleapis.com/css2?family=Oswald:wght@500;600;700&family=Roboto:wght@400;500;700&display=swap" rel="stylesheet">
<style>
:root{
  --red:#d4302a;
  --orange:#e5621f;
  --ink:#111111;
  --text:#555555;
  --white:#ffffff;
  --ghost:#efefef;
  --dark:#151515;
  --product:#2b2b2b;
  --card-shadow:0 2px 10px rgba(0,0,0,.18);
}
*{margin:0;padding:0;box-sizing:border-box}
html,body{width:1200px;height:4159px;overflow:hidden}
body{position:relative;font-family:'Roboto',sans-serif;color:var(--text);background:var(--white)}
.photo{position:absolute;display:block}
.display{font-family:'Oswald',sans-serif}

/* header + hero */
.hero{position:absolute;left:0;top:0;width:1200px;height:685px;overflow:hidden}
.hero-photo{inset:0;width:100%;height:100%;background:radial-gradient(ellipse at 60% 85%,#b84a12 0%,#5a2a12 18%,#1f1c1b 45%,#0f0f0f 100%)}
.brand{position:absolute;display:flex;align-items:center;gap:12px;font-family:'Oswald',sans-serif;font-weight:600;color:var(--white);letter-spacing:1px}
.brand-dot{width:34px;height:34px;border-radius:50%;background:var(--red)}
.hero .brand{left:110px;top:24px;font-size:44px;line-height:1}
.nav{position:absolute;left:463px;top:38px;display:flex;gap:28px;font-size:14px;font-weight:500;color:var(--white)}
.nav .active{color:var(--orange);border-bottom:2px solid var(--orange);padding-bottom:4px}
.btn{position:absolute;display:flex;align-items:center;justify-content:center;color:var(--white);font-weight:700;border-radius:22px;background:linear-gradient(90deg,var(--red),var(--orange))}
.btn-start{left:945px;top:26px;width:144px;height:42px;font-size:14px}
.hero-ghost{position:absolute;left:0;width:1200px;top:190px;text-align:center;font-size:200px;font-weight:700;color:rgba(255,255,255,.04);line-height:1}
.hero-kicker{position:absolute;left:0;width:1200px;top:200px;text-align:center;font-size:15px;letter-spacing:6px;color:var(--orange);font-weight:600}
.hero-title{position:absolute;left:0;width:1200px;top:220px;text-align:center;font-size:64px;font-weight:600;color:var(--white);line-height:1.1}
.btn-book{left:528px;top:312px;width:144px;height:42px;font-size:13px;background:var(--red)}
.hero-arrow{position:absolute;top:272px;width:38px;height:38px;border-radius:50%;background:rgba(0,0,0,.7)}
.down{position:absolute;left:573px;top:530px;width:54px;height:54px;border-radius:50%;background:var(--orange)}

/* about */
.ghost{position:absolute;left:0;width:1200px;text-align:center;font-family:'Oswald',sans-serif;font-weight:700;font-size:130px;color:var(--ghost);line-height:1}
.kicker{font-size:14px;letter-spacing:5px;color:var(--orange);font-weight:600}
.about-copy{position:absolute;left:110px;top:786px;width:476px}
.about-copy h2{font-family:'Oswald',sans-serif;font-weight:600;font-size:40px;color:var(--ink);margin:12px 0 14px}
.about-copy p{font-size:14px;line-height:26px;text-align:justify;margin-bottom:26px}
.btn-read{left:110px;top:1158px;width:145px;height:42px;font-size:14px;background:var(--red)}
.about-photo{left:620px;top:790px;width:469px;height:410px;background:linear-gradient(135deg,#6b5a2c,#c9762a 45%,#2f4a1d)}

/* promo */
.promo-photo{left:0;top:1286px;width:1200px;height:518px;background:linear-gradient(180deg,#111 0%,#2a1a12 40%,#7a3a18 75%,#4a2614 100%)}
.promo-tag{position:absolute;left:383px;top:1357px;width:420px;height:84px;background:var(--red);color:var(--white);font-family:'Oswald',sans-serif;font-weight:600;font-size:40px;display:flex;align-items:center;justify-content:center}

/* products */
.section-title{position:absolute;left:0;width:1200px;text-align:center;font-family:'Oswald',sans-serif;font-weight:600;font-size:40px;color:var(--ink)}
.card{position:absolute;top:1957px;width:474px;height:475px;background:var(--white);border-radius:10px;box-shadow:var(--card-shadow);overflow:hidden}
.card-photo{left:24px;top:20px;width:426px;height:330px;border-radius:6px;background:linear-gradient(180deg,#e9e9e9,#d4d4d4)}
.card-label{position:absolute;left:0;top:365px;width:312px;height:73px;border-radius:0 37px 37px 0;background:var(--orange);color:var(--white);font-family:'Oswald',sans-serif;font-weight:500;font-size:24px;display:flex;align-items:center;justify-content:center}
.chev{position:absolute;top:2145px}

/* testimonial */
.review-photo{left:0;top:2519px;width:1200px;height:458px;background:linear-gradient(90deg,#4f7a33,#8a6a4a 40%,#5a3a2a 60%,#c07a35 80%,#a9b7a0)}
.quote-card{position:absolute;left:111px;top:2615px;width:488px;height:265px;background:var(--white);padding:26px 28px}
.quote-card p{font-size:14px;line-height:26px;text-align:justify}
.author{position:absolute;left:28px;top:196px;display:flex;align-items:center;gap:12px}
.avatar{width:50px;height:50px;border-radius:50%;background:#9a9a9a}
.author b{display:block;font-size:16px;color:var(--ink);font-weight:500}
.author span{font-size:12px}
.quote-mark{position:absolute;right:28px;top:196px}

/* follow */
.tile{position:absolute;border-radius:6px}

/* footer */
.footer{position:absolute;left:0;top:3789px;width:1200px;height:370px;background:linear-gradient(180deg,#1c1c1c,#0c0c0c);color:var(--white)}
.footer .brand{left:455px;top:42px;font-size:44px;line-height:1}
.foot-nav{position:absolute;left:0;width:1200px;top:124px;text-align:center;font-size:13px;font-weight:700}
.foot-nav span{margin:0 12px}
.contact{position:absolute;top:180px;display:flex;gap:20px}
.contact i{width:52px;height:52px;border-radius:50%;background:var(--white);display:flex;align-items:center;justify-content:center;flex:none}
.contact h4{font-size:20px;font-weight:500}
.contact p{font-size:13px;line-height:26px;width:175px}
.socials{position:absolute;left:535px;top:4067px;display:flex;gap:6px}
.socials i{width:28px;height:28px;border:1px solid var(--white);border-radius:50%;display:block}
.copy{position:absolute;left:0;width:1200px;top:4117px;text-align:center;font-size:13px;color:var(--white)}
</style>
</head>
<body>

<header class="hero">
  <div class="photo hero-photo" role="img" aria-label="Open charcoal grill with flames rising from the grate"></div>
  <div class="hero-ghost display">FIAMMEO</div>
  <div class="brand"><span class="brand-dot"></span>FIAMMEO</div>
  <nav class="nav"><span class="active">Home</span><span>About us</span><span>Menus</span><span>Reviews</span><span>Blog</span><span>Contact us</span></nav>
  <a class="btn btn-start">Get Started</a>
  <div class="hero-kicker display">WELCOME TO</div>
  <h1 class="hero-title display">Fiammeo</h1>
  <a class="btn btn-book">BOOK NOW</a>
  <span class="hero-arrow" style="left:70px"><svg width="38" height="38"><path d="M22 13l-6 6 6 6" stroke="#fff" stroke-width="2" fill="none"/></svg></span>
  <span class="hero-arrow" style="left:1089px"><svg width="38" height="38"><path d="M16 13l6 6-6 6" stroke="#fff" stroke-width="2" fill="none"/></svg></span>
  <span class="down"><svg width="54" height="54"><path d="M27 16v22M19 30l8 8 8-8" stroke="#fff" stroke-width="2.5" fill="none"/></svg></span>
</header>

<section class="about">
  <div class="ghost" style="top:680px">ABOUT US</div>
  <div class="about-copy">
    <div class="kicker display">ABOUT US</div>
    <h2>Fiammeo</h2>
    <p>Lorem ipsum dolor sit amet, consectetur adipiscing elit, sed do eiusmod tempor incididunt ut labore et dolore magna aliqua. Ut enim ad minim veniam, quis nostrud exercitation ullamco laboris nisi ut aliquip ex ea commodo consequat. Duis aute irure dolor in reprehenderit in voluptate velit esse cillum dolore eu fugiat nulla pariatur.</p>
    <p>Excepteur sint occaecat cupidatat non proident, sunt in culpa qui officia deserunt mollit anim id est laborum. Lorem ipsum dolor sit amet, consectetur adipiscing elit, sed do eiusmod tempor incididunt ut labore et dolore magna aliqua.</p>
  </div>
  <a class="btn btn-read">Read more &#8594;</a>
  <div class="photo about-photo" role="img" aria-label="Kettle grill with open flames on a lawn, split by a diagonal white line"></div>
</section>

<section class="promo">
  <div class="photo promo-photo" role="img" aria-label="Steaks, sausages, tomatoes and vegetables sizzling on a grill"></div>
  <div class="promo-tag">Save the Amount 50%</div>
</section>

<section class="products">
  <div class="ghost" style="top:1822px">OUR PRODUCT</div>
  <h2 class="section-title" style="top:1878px">Our Product</h2>
  <svg class="chev" style="left:40px" width="34" height="56"><path d="M30 2L4 28l26 26" stroke="#111" stroke-width="3" fill="none"/></svg>
  <svg class="chev" style="left:1126px" width="34" height="56"><path d="M4 2l26 26L4 54" stroke="#111" stroke-width="3" fill="none"/></svg>
  <article class="card" style="left:111px">
    <div class="photo card-photo" role="img" aria-label="Product photo: black ceramic grill on a stand"></div>
    <div class="card-label">NEMO ENIM IPSAM</div>
  </article>
  <article class="card" style="left:615px">
    <div class="photo card-photo" role="img" aria-label="Product photo: close view of a ceramic grill base"></div>
    <div class="card-label">NEMO ENIM IPSAM</div>
  </article>
</section>

<section class="review">
  <div class="photo review-photo" role="img" aria-label="People grilling sausages and meat outdoors"></div>
  <blockquote class="quote-card">
    <p>“Lorem ipsum dolor sit amet, consectetur adipiscing elit, sed do eiusmod tempor incididunt ut labore et dolore magna aliqua. Ut enim ad minim veniam, quis nostrud exercitation ullamco laboris nisi ut aliquip ex ea commodo consequat. Lorem ipsum dolor sit ad minim veniam, quis nostrud exercitation ullamco laboris nisi ut aliquip ex ea commodo consequat.”</p>
    <div class="author"><span class="avatar" role="img" aria-label="Customer portrait"></span><div><b>John doe</b><span>Company name</span></div></div>
    <svg class="quote-mark" width="58" height="48" viewBox="0 0 58 48"><path d="M24 4C10 8 2 18 2 30c0 9 5 16 12 16 6 0 10-4 10-10s-4-10-10-10c-1 0-2 0-3 .3C12 19 17 13 26 10zM56 4C42 8 34 18 34 30c0 9 5 16 12 16 6 0 10-4 10-10s-4-10-10-10c-1 0-2 0-3 .3C44 19 49 13 58 10z" fill="var(--red)"/></svg>
  </blockquote>
</section>

<section class="follow">
  <div class="ghost" style="top:2982px">FOLLOW US</div>
  <h2 class="section-title" style="top:3048px">Follow Us @fiammeo</h2>
  <div class="tile" style="left:111px;top:3130px;width:315px;height:213px;background:linear-gradient(135deg,#5f8a3c,#b7a98a)" role="img" aria-label="Friends camping around a grill"></div>
  <div class="tile" style="left:111px;top:3361px;width:315px;height:341px;background:linear-gradient(160deg,#5a2a14,#c0581c 60%,#2a160c)" role="img" aria-label="Steaks with rosemary over flames"></div>
  <div class="tile" style="left:444px;top:3130px;width:315px;height:342px;background:linear-gradient(160deg,#2e3a4a,#44506a 50%,#a0552a)" role="img" aria-label="Person turning skewers on a grill"></div>
  <div class="tile" style="left:444px;top:3488px;width:315px;height:214px;background:linear-gradient(135deg,#2a2a2a,#c48a2a 50%,#2f6a6a)" role="img" aria-label="Grilled vegetables and dishes on a table"></div>
  <div class="tile" style="left:774px;top:3130px;width:315px;height:213px;background:linear-gradient(135deg,#6a7a5a,#3a3230 50%,#8a5a3a)" role="img" aria-label="Tongs lifting meat from an outdoor grill"></div>
  <div class="tile" style="left:774px;top:3361px;width:315px;height:341px;background:linear-gradient(160deg,#4a4a4a,#8a7a6a 45%,#5a2e1a)" role="img" aria-label="Smoky grill with sausages and meat at night"></div>
</section>

<footer class="footer">
  <div class="brand"><span class="brand-dot"></span>FIAMMEO</div>
  <div class="foot-nav">HOME<span>|</span>ABOUT US<span>|</span>MENUS<span>|</span>REVIEWS<span>|</span>BLOG<span>|</span>CONTACT US</div>
  <div class="contact" style="left:237px"><i><svg width="20" height="24"><path d="M10 1a8 8 0 0 0-8 8c0 6 8 14 8 14s8-8 8-14a8 8 0 0 0-8-8zm0 11a3 3 0 1 1 0-6 3 3 0 0 1 0 6z" fill="var(--red)"/></svg></i><div><h4>Address :</h4><p>Lorem ipsum dolor sit am et, consec</p></div></div>
  <div class="contact" style="left:512px"><i><svg width="24" height="18"><rect x="1" y="1" width="22" height="16" rx="2" fill="var(--red)"/><path d="M2 3l10 7 10-7" stroke="#fff" stroke-width="1.6" fill="none"/></svg></i><div><h4>Email Address :</h4><p>info@companyname.com</p></div></div>
  <div class="contact" style="left:777px"><i><svg width="22" height="22"><path d="M5 2l4 1 1 5-3 2a12 12 0 0 0 5 5l2-3 5 1 1 4c0 2-2 3-3 3C9 20 2 13 2 5c0-1 1-3 3-3z" fill="var(--red)"/></svg></i><div><h4>Phone :</h4><p>+1 888 888 8888</p></div></div>
</footer>
<div class="socials"><i></i><i></i><i></i><i></i></div>
<div class="copy">Copyright © 2023. All Rights Reserved</div>

</body>
</html>
```